Dusty Spur Outfitters Home Page

I need a logo and page design for my home page, maybe some background color suggestions to go with it. I want the logo to project "vintage" and "western wear" but not be your typical trite western saddle and gun type thing.
http://www.dustyspuroutfitters.example/store/cart.php
Not looking for page coding just logo and other design elements to lay in over the site's template to make it "pop"
Reason: Have to finalize the design.
Target Market(s)
My customers are 70/30 men to women.
Industry/Entity Type
Gun

```html
<!DOCTYPE html>
<html lang="en">
<head>
<meta charset="utf-8">
<title>Dusty Spur Outfitters – Header Options</title>
<link rel="stylesheet" href="https://fonts.googleapis.com/css2?family=Lato:wght@700;900&family=Damion&display=swap">
<style>
  :root {
    --linen: #d3c2a2;
    --linen-dark: #c8b695;
    --band-black: #1b1a19;
    --slate: #2c2c2c;
    --slate-light: #3b3b3b;
    --teal: #2f727a;
    --leather: #17161b;
    --cream: #e6dcc4;
    --cream-text: #d9d0b8;
    --ink: #2b2a28;
    --rust: #a3281c;
  }
  html, body {
    margin: 0;
    padding: 0;
    width: 1200px;
    height: 1000px;
    overflow: hidden;
  }
  body {
    position: relative;
    background:
      repeating-linear-gradient(0deg, rgba(255,255,255,0.05) 0 1px, transparent 1px 3px),
      repeating-linear-gradient(90deg, rgba(0,0,0,0.04) 0 1px, transparent 1px 3px),
      var(--linen);
    font-family: "Lato", sans-serif;
  }
  .header-band {
    position: absolute;
    left: 0;
    width: 1200px;
    height: 165px;
    box-shadow: 0 3px 5px rgba(0,0,0,0.35);
    overflow: hidden;
  }
  .header-band--distressed { top: 147px; background: var(--band-black); }
  .header-band--teal { top: 417px; background: var(--teal); }
  .header-band--leather {
    top: 687px;
    background:
      radial-gradient(ellipse at 30% 60%, rgba(255,255,255,0.05), transparent 60%),
      radial-gradient(ellipse at 75% 30%, rgba(255,255,255,0.04), transparent 55%),
      repeating-radial-gradient(circle at 40% 50%, rgba(255,255,255,0.025) 0 1px, transparent 1px 3px),
      var(--leather);
  }
  .band-inner {
    position: absolute;
    left: 0;
    right: 0;
    top: 16px;
    bottom: 16px;
    background:
      radial-gradient(ellipse at 20% 40%, rgba(110,110,110,0.35), transparent 55%),
      radial-gradient(ellipse at 60% 70%, rgba(90,90,90,0.3), transparent 50%),
      radial-gradient(ellipse at 85% 30%, rgba(100,100,100,0.25), transparent 45%),
      var(--slate);
  }
  .header-band--teal .band-inner { top: 15px; bottom: 15px; }
  .brand {
    position: absolute;
    left: 60px;
    top: 0;
    width: 405px;
    height: 165px;
    display: flex;
    align-items: center;
    justify-content: center;
    gap: 12px;
  }
  .brand-mark {
    width: 22px;
    height: 22px;
    border-radius: 50%;
    background: var(--rust);
    flex: none;
  }
  .brand-name {
    font-family: "Lato", sans-serif;
    font-weight: 900;
    font-size: 34px;
    color: var(--cream);
    white-space: nowrap;
  }
  .tagline {
    position: absolute;
    left: 476px;
    top: 86px;
    margin: 0;
    font-family: "Damion", cursive;
    font-size: 25px;
    line-height: 1;
    color: var(--cream-text);
    text-shadow: 1px 1px 1px rgba(0,0,0,0.6);
    white-space: nowrap;
  }
  .search {
    position: absolute;
    left: 901px;
    top: 51px;
    display: flex;
    align-items: center;
  }
  .search-field {
    width: 173px;
    height: 30px;
    box-sizing: border-box;
    padding: 0 17px;
    border-radius: 15px;
    background: var(--cream);
    color: var(--ink);
    font-weight: 700;
    font-size: 17px;
    line-height: 30px;
  }
  .search-go {
    margin-left: 10px;
    color: var(--cream-text);
    font-weight: 700;
    font-size: 18px;
  }
</style>
</head>
<body>

  <header class="header-band header-band--distressed">
    <div class="band-inner"></div>
    <div class="brand"><span class="brand-mark"></span><span class="brand-name">Dusty Spur Outfitters</span></div>
    <p class="tagline">Brand-New Retro Styled Western Wear</p>
    <div class="search"><div class="search-field">Search...</div><span class="search-go">GO!</span></div>
  </header>

  <header class="header-band header-band--teal">
    <div class="band-inner"></div>
    <div class="brand"><span class="brand-mark"></span><span class="brand-name">Dusty Spur Outfitters</span></div>
    <p class="tagline">Brand-New Retro Styled Western Wear</p>
    <div class="search"><div class="search-field">Search...</div><span class="search-go">GO!</span></div>
  </header>

  <header class="header-band header-band--leather">
    <div class="brand"><span class="brand-mark"></span><span class="brand-name">Dusty Spur Outfitters</span></div>
    <p class="tagline">Brand-New Retro Styled Western Wear</p>
    <div class="search"><div class="search-field">Search...</div><span class="search-go">GO!</span></div>
  </header>

</body>
</html>
```